Professional and creative business card design for recruiting service providers

Our company supports German medium-sized companies in filling vacancies promptly. For this we use social media marketing and bring our customers into the visibility.

We want a professional but also creative design for our business cards.

Please look at lindqvar-staff.de to get an impression of our CI.

Target Market(s)

Small and medium-sized companies in Germany from the industry

Industry/Entity Type

Industrie, Handwerk

Contact Information for Business Card

Name, Position, Telefonnummer, Email, Website

Colors
EE7325
F08F49
F5BC92
FAE3D3
FDF4ED

Requirements
Must have
• A picture of the employee and in the style of www.lindqvar-staff.de

```html
<!DOCTYPE html>
<html lang="de">
<head>
<meta charset="utf-8">
<title>Lindqvar &amp; Staff – Visitenkarte</title>
<link rel="stylesheet" href="https://fonts.googleapis.com/css2?family=Montserrat:wght@800&family=Lato:wght@400&display=swap">
<style>
  :root {
    --stage: #2a2a2a;
    --card-white: #ffffff;
    --brand-orange: #f0602c;
    --ink: #111111;
    --text-on-orange: #ffffff;
  }
  html, body {
    margin: 0;
    padding: 0;
    width: 1200px;
    height: 1015px;
    overflow: hidden;
    background: var(--stage);
  }
  .canvas {
    position: relative;
    width: 1200px;
    height: 1015px;
  }
  .card {
    position: absolute;
    width: 560px;
    height: 320px;
    overflow: hidden;
    box-shadow: 0 12px 30px rgba(0,0,0,0.55);
  }
  /* Front side */
  .card-front {
    left: 90px;
    top: 110px;
    background: var(--card-white);
    display: flex;
    align-items: center;
    justify-content: center;
    gap: 22px;
  }
  .brand-square {
    width: 54px;
    height: 54px;
    background: var(--brand-orange);
  }
  .brand-name {
    font-family: "Montserrat", sans-serif;
    font-weight: 800;
    font-size: 34px;
    line-height: 1.05;
    letter-spacing: 2px;
    color: var(--ink);
    margin: 0;
  }
  /* Back side */
  .card-back {
    left: 550px;
    top: 540px;
    background: var(--brand-orange);
  }
  .portrait-frame {
    position: absolute;
    inset: 0;
    z-index: 0;
  }
  .person {
    position: absolute;
    left: 34px;
    top: 112px;
    z-index: 1;
    color: var(--text-on-orange);
  }
  .person-name {
    font-family: "Montserrat", sans-serif;
    font-weight: 800;
    font-size: 22px;
    letter-spacing: 0;
    margin: 0;
    white-space: nowrap;
  }
  .person-role {
    font-family: "Lato", sans-serif;
    font-size: 16px;
    margin: 2px 0 0;
  }
  .contact-list {
    position: absolute;
    left: 34px;
    bottom: 26px;
    z-index: 1;
    margin: 0;
    padding: 0;
    list-style: none;
    font-family: "Lato", sans-serif;
    font-size: 15px;
    color: var(--text-on-orange);
  }
  .contact-list li {
    display: flex;
    align-items: center;
    gap: 9px;
    line-height: 24px;
  }
  .contact-icon {
    width: 15px;
    height: 15px;
    flex: none;
  }
</style>
</head>
<body>
<main class="canvas">

  <section class="card card-front" aria-label="Vorderseite">
    <div class="brand-square"></div>
    <p class="brand-name">LINDQVAR<br>&amp; STAFF</p>
  </section>

  <section class="card card-back" aria-label="Rückseite">
    <svg class="portrait-frame" viewBox="0 0 560 320" width="560" height="320">
      <defs>
        <radialGradient id="portrait-tone" cx="62%" cy="70%" r="70%">
          <stop offset="0%" stop-color="#5e5e64"/>
          <stop offset="45%" stop-color="#bdbdbd"/>
          <stop offset="100%" stop-color="#f4f4f4"/>
        </radialGradient>
      </defs>
      <path d="M340 0 H560 V320 H500 Z" fill="#ffffff"/>
      <circle cx="425" cy="100" r="165" fill="#ffffff"/>
      <path d="M276 46 A158 158 0 0 0 452 256" fill="none" stroke="#111111" stroke-width="6"/>
      <circle cx="428" cy="98" r="150" fill="url(#portrait-tone)" role="img" aria-label="Porträtfoto des Mitarbeiters im dunklen Sakko"/>
    </svg>

    <div class="person">
      <h1 class="person-name">HENRIK VOLLMER</h1>
      <p class="person-role">Managing Director</p>
    </div>

    <ul class="contact-list">
      <li>
        <svg class="contact-icon" viewBox="0 0 16 16" aria-hidden="true"><path d="M3 1.5l2.5 0 1.2 3-1.6 1.2c.8 1.8 2.4 3.4 4.2 4.2l1.2-1.6 3 1.2v2.5c0 .8-.7 1.5-1.5 1.5C6.5 13.5 2.5 9.5 1.5 3 1.5 2.2 2.2 1.5 3 1.5z" fill="#fff"/></svg>
        040-987 654 321
      </li>
      <li>
        <svg class="contact-icon" viewBox="0 0 16 16" aria-hidden="true"><rect x="1" y="3" width="14" height="10" fill="none" stroke="#fff" stroke-width="1.5"/><path d="M1 3l7 6 7-6" fill="none" stroke="#fff" stroke-width="1.5"/></svg>
        info@lindqvar-staff.de
      </li>
      <li>
        <svg class="contact-icon" viewBox="0 0 16 16" aria-hidden="true"><circle cx="8" cy="8" r="6.5" fill="none" stroke="#fff" stroke-width="1.3"/><ellipse cx="8" cy="8" rx="3" ry="6.5" fill="none" stroke="#fff" stroke-width="1.1"/><path d="M1.5 8h13M2.5 5h11M2.5 11h11" stroke="#fff" stroke-width="1"/></svg>
        www.lindqvar-staff.de
      </li>
    </ul>
  </section>

</main>
</body>
</html>
```